Gentle Harvest Scripture Cards

I need a package designed for the upright top hinged flip lid cardboard box that is going to store my 100 bible verse flashcards. The approximate size will be 4.3 in. Wide X 6.25 in. Tall X 2 in. deep. I am going to have it in Matte finish with the name Gentle Harvest in spot UV on the front of the box. This project will appeal mostly to women, so the design should be along the feminine lines. My logo color has pink, purple and blue in it. Watercolors may be a possibility for use on the package. I am attaching pictures of a similar type box to give you an idea of the shape only of a top hinged lid box. I am also attaching the logo Gentle Harvest Scripture centered insight to comfort and refresh the heart that will be on the front of the box, and text of the product description that I need on the back of the box. The last 2 watercolor design pictures that are attached are for inspiration as I like the design and color scheme in those pictures. Thank you for your time. Marianne
**Update** On one side of the box please put "9 prayers included" and on the other side of the box put "Scan the included QR code to download a prayer devotional"

Target Market(s)

Women between the ages of 25-75yrs

Industry/Entity Type

Religious/Spirituality

Font styles to use
Serif
Other font styles liked:
• I like decorative font, but dont want too much extra designs, just the letters

Colors
0094D4
00A9DD
6FCCEA
C7EBF8
E9F6FB
A7469A
B969AE
D3A5CF
EDDBEB
F8F0F9
6B429C
8869AF
B7A5CE
E3DAEB
F3F0F8

Requirements
Must have
• The colors of pink, purple and blue incorporated into the design
Nice to have
• Maybe some watercolors, floral or landscape-y designs
Should not have
• Do not want red in my packaging

```html
<!DOCTYPE html>
<html lang="en">
<head>
<meta charset="utf-8">
<title>Gentle Harvest Scripture Cards – Box Panels</title>
<link href="https://fonts.googleapis.com/css2?family=Oswald:wght@400;500;600&family=Playfair+Display:ital,wght@0,700;1,400&family=Poppins:wght@500&family=Inter:wght@400&display=swap" rel="stylesheet">
<style>
  :root {
    --sky: #7cb8ea;
    --sky-light: #a9cdf0;
    --lavender: #c7b3dc;
    --blush: #eccbe2;
    --pink: #e58cc0;
    --magenta: #a7269a;
    --accent-pink: #c8237f;
    --purple: #4f2a86;
    --plum: #6b429c;
    --cyan: #00a9dd;
    --paper: #fbf6fb;
    --stage: #f3f0f4;
    --floral-a: #d3a5cf;
    --floral-b: #eddbeb;
    --floral-c: #e3dacb;
  }
  * { margin: 0; padding: 0; box-sizing: border-box; }
  html, body { width: 1200px; height: 800px; overflow: hidden; }
  body { background: var(--stage); position: relative; font-family: "Inter", sans-serif; }

  .panel {
    position: absolute;
    overflow: hidden;
    background: linear-gradient(180deg, var(--sky) 0%, var(--lavender) 38%, var(--blush) 62%, var(--pink) 100%);
  }
  .panel::after {
    content: "";
    position: absolute; left: 0; right: 0; bottom: 0; height: 45%;
    background: repeating-linear-gradient(176deg, rgba(255,255,255,0) 0 22px, rgba(255,255,255,0.22) 22px 26px);
    pointer-events: none;
  }

  /* lid */
  .lid { left: 297px; top: 110px; width: 303px; height: 141px;
    background: linear-gradient(180deg, var(--sky) 0%, var(--sky-light) 40%, var(--blush) 100%); }
  .lid .brand-name { position: absolute; top: 42px; width: 100%; text-align: center; font-size: 34px; }
  .lid .tagline { position: absolute; top: 92px; width: 100%; text-align: center; font-size: 9.5px; color: var(--cyan); }

  .brand-name { font-family: "Playfair Display", serif; font-weight: 700; color: var(--plum); line-height: 1; }
  .tagline { font-family: "Inter", sans-serif; }

  /* panels */
  .side-left  { left: 156px; top: 251px; width: 141px; height: 440px; }
  .front      { left: 297px; top: 251px; width: 303px; height: 440px; }
  .side-right { left: 600px; top: 251px; width: 141px; height: 440px; }
  .back       { left: 741px; top: 251px; width: 303px; height: 440px; }

  .front .collar { position: absolute; top: 0; left: 0; right: 0; height: 22px; background: var(--magenta); }

  .floral { position: absolute; z-index: 1; }
  .front .floral-wreath { left: 22px; top: 60px; width: 260px; height: 280px; border-radius: 50%;
    background: radial-gradient(ellipse at center, var(--floral-a) 0%, var(--floral-b) 60%, rgba(237,219,235,0) 75%); }
  .front .badge { position: absolute; z-index: 2; left: 46px; top: 90px; width: 212px; height: 212px; border-radius: 50%;
    background: var(--paper); border: 2px solid var(--plum); padding: 36px 20px 0 26px; }
  .badge .brand-name { font-size: 22px; text-align: center; margin-left: -6px; }
  .badge .lead { font-family: "Playfair Display", serif; font-style: italic; font-size: 15px; color: var(--purple); margin: 8px 0 6px; }
  .badge .uses { list-style: none; font-family: "Poppins", sans-serif; font-weight: 500; font-size: 13px; color: var(--accent-pink); line-height: 1.45; padding-left: 8px; }

  .count-line { position: absolute; z-index: 3; left: 78px; top: 318px; display: flex; align-items: center; gap: 6px; }
  .count-line .big { font-family: "Oswald", sans-serif; font-weight: 600; font-size: 62px; color: var(--purple); line-height: 1; }
  .count-line .label { font-family: "Oswald", sans-serif; font-weight: 500; font-size: 19px; color: var(--accent-pink); line-height: 1.15; }

  /* sides */
  .side { text-align: center; }
  .side .brand-name { position: relative; z-index: 2; margin-top: 56px; font-size: 17px; line-height: 1.1; }
  .side .big { position: relative; z-index: 2; display: block; font-family: "Oswald", sans-serif; font-weight: 600; font-size: 52px; color: var(--purple); line-height: 1; margin-top: 24px; }
  .side .label { position: relative; z-index: 2; display: block; font-family: "Oswald", sans-serif; font-weight: 400; font-size: 17px; line-height: 1.35; }
  .side-left .label { color: var(--purple); }
  .side-right .label { color: var(--accent-pink); }
  .side-left .prayer-count { position: relative; z-index: 2; display: block; font-family: "Oswald", sans-serif; font-weight: 600; font-size: 50px; color: var(--accent-pink); line-height: 1; margin-top: 10px; }
  .side-left .prayer-label { position: relative; z-index: 2; display: block; font-family: "Oswald", sans-serif; font-weight: 500; font-size: 22px; color: var(--accent-pink); line-height: 1.2; }
  .side-right .scan-note { position: relative; z-index: 2; margin-top: 38px; font-family: "Oswald", sans-serif; font-weight: 400; font-size: 15px; color: var(--purple); line-height: 1.4; padding: 0 10px; }
  .side-right .scan-note .hl { color: var(--accent-pink); font-size: 17px; display: block; }
  .side .floral-foot { left: 0; right: 0; bottom: 0; height: 90px;
    background: linear-gradient(180deg, rgba(211,165,207,0) 0%, var(--floral-a) 100%); }

  /* back */
  .back .frame { position: absolute; z-index: 2; left: 0; top: 0; }
  .back .floral-top { left: 20px; top: 22px; width: 190px; height: 120px; border-radius: 50%;
    background: radial-gradient(ellipse at center, var(--floral-c) 0%, rgba(227,218,203,0.6) 50%, rgba(227,218,203,0) 75%); }
  .back .floral-bottom { right: 6px; bottom: 18px; width: 200px; height: 130px; border-radius: 50%;
    background: radial-gradient(ellipse at center, #e8f0f8 0%, rgba(232,240,248,0.6) 50%, rgba(232,240,248,0) 75%); }
  .back .copy { position: absolute; z-index: 3; left: 56px; top: 112px; width: 196px; }
  .back .brand-name { font-size: 22px; text-align: center; }
  .back .tagline { font-size: 6px; color: var(--cyan); text-align: center; margin-top: 4px; }
  .back .description { font-size: 11.5px; color: #2b2233; line-height: 1.42; margin-top: 14px; }
</style>
</head>
<body>

  <section class="panel lid" aria-label="Lid top">
    <p class="brand-name">Gentle Harvest</p>
    <p class="tagline">Scripture centered insight to comfort and refresh the heart</p>
  </section>

  <section class="panel side side-left" aria-label="Left side panel">
    <p class="brand-name">Gentle<br>Harvest</p>
    <span class="big">100</span>
    <span class="label">BIBLE VERSE</span>
    <span class="label">FLASHCARDS</span>
    <span class="prayer-count">9</span>
    <span class="prayer-label">PRAYERS<br>INCLUDED</span>
    <div class="floral floral-foot" role="img" aria-label="Watercolour floral sprigs along the base"></div>
  </section>

  <section class="panel front" aria-label="Front panel">
    <div class="collar"></div>
    <div class="floral floral-wreath" role="img" aria-label="Watercolour floral wreath with leaves and birds"></div>
    <div class="badge">
      <p class="brand-name">Gentle Harvest</p>
      <p class="lead">Bible Based Wisdom For:</p>
      <ul class="uses">
        <li>Personal reflection</li>
        <li>Spiritual growth</li>
        <li>Navigating Life’s<br>Challenges</li>
      </ul>
    </div>
    <div class="count-line">
      <span class="big">100</span>
      <span class="label">BIBLE VERSE<br>FLASHCARDS</span>
    </div>
  </section>

  <section class="panel side side-right" aria-label="Right side panel">
    <p class="brand-name">Gentle<br>Harvest</p>
    <span class="big">100</span>
    <span class="label">BIBLE VERSE</span>
    <span class="label">FLASHCARDS</span>
    <p class="scan-note">Scan included <span class="hl">QR code</span>to download a prayer devotional</p>
    <div class="floral floral-foot" role="img" aria-label="Watercolour floral sprigs along the base"></div>
  </section>

  <section class="panel back" aria-label="Back panel">
    <div class="floral floral-top" role="img" aria-label="Soft watercolour flowers and leaves, upper corner"></div>
    <div class="floral floral-bottom" role="img" aria-label="Soft watercolour white blossoms, lower corner"></div>
    <svg class="frame" width="303" height="440" viewBox="0 0 303 440" aria-hidden="true">
      <polygon points="151,40 280,150 280,330 151,420 22,330 22,150" fill="rgba(251,246,251,0.9)" stroke="#c8237f" stroke-width="1.5"/>
      <polygon points="176,60 296,180 286,350 150,430 12,320 30,140" fill="none" stroke="#6b429c" stroke-width="0.8"/>
    </svg>
    <div class="copy">
      <p class="brand-name">Gentle Harvest</p>
      <p class="tagline">Scripture centered insight to comfort and refresh the heart</p>
      <p class="description">Unlock personal growth and guidance with our premium 100-card collection. Organized by common life difficulties, each card provides encouragement, inspiration, and biblical wisdom for daily reflection. Perfect for personal and group use, this collection offers practical insights and advice for applying biblical teachings to daily life.</p>
    </div>
  </section>

</body>
</html>
```